VORLAND COMPOSITES INC website in USA

VORLAND COMPOSITES INC incorporated and operated in USA needs a completely new design of website. This Wyoming based company is a importer and distributor of composites material to supply mainly to American and Canadian/Mexican customers. Our main products includes Carbon Fiber, Aramid Fiber, Glass Fiber, Basalt Fiber, High Silica Glass, Quartz Fiber, S-Glass, Alumina Fiber, Vacuum Auxiliary.

We are one stop composites solution provider for Automotive, Aerospace, Construction, Electrical and Machinery industries.

We are exclusive sales company in North America for BLORAN composites produced from China and their other Asia facilities.

Target Market(s)

USA and Canada

Industry/Entity Type

Composites materials

Coding

Coded - Design and coding required

Number of Pages Required

5+ page

Requirements
Nice to have
• Color theme to match our corporate logo VORLAND. VORLAND stands for Northgate Provisioning Trade Holdings

```html
<!DOCTYPE html>
<html lang="en">
<head>
<meta charset="utf-8">
<title>Vorland Composites Inc</title>
<link href="https://fonts.googleapis.com/css2?family=Montserrat:wght@400;500;600;700;800&display=swap" rel="stylesheet">
<style>
:root{
  --orange:#E8862A;
  --ink:#2A2623;
  --text:#3A3A3A;
  --muted:#555;
  --white:#fff;
  --card-shadow:0 4px 14px rgba(0,0,0,.12);
}
*{box-sizing:border-box;margin:0;padding:0}
html,body{width:1200px;height:4208px;overflow:hidden}
body{position:relative;background:var(--white);font-family:'Montserrat',sans-serif;color:var(--text)}
.abs{position:absolute}
.btn{position:absolute;display:flex;align-items:center;justify-content:center;background:var(--orange);color:var(--white);font-weight:700;font-size:14px;border-radius:22px;letter-spacing:.3px}

/* header */
.header{position:absolute;left:0;top:0;width:1200px;height:120px;background:var(--white);border-top:2px solid var(--orange);z-index:3}
.phone-tab{position:absolute;left:650px;top:0;width:431px;height:38px;background:var(--orange);border-radius:0 0 10px 10px;display:flex;align-items:center;justify-content:center;gap:14px;color:var(--white);font-size:14px;font-weight:700}
.phone-tab span.num{font-weight:500}
.phone-tab .sep{width:1.5px;height:26px;background:var(--white)}
.brand{position:absolute;left:90px;top:36px;display:flex;align-items:center;gap:14px}
.brand-dot{width:18px;height:18px;border-radius:50%;background:var(--orange)}
.brand-name{font-size:38px;font-weight:800;color:var(--ink);letter-spacing:1px}
.brand-rule{width:1.5px;height:56px;background:var(--ink)}
.brand-tag{font-size:11px;line-height:15px;color:var(--ink);width:112px}
.nav{position:absolute;left:445px;top:71px;display:flex;gap:20px;font-size:13px;color:var(--ink);font-weight:500}
.nav .active{color:var(--orange);border-bottom:2px solid var(--orange);padding-bottom:8px}
.contact-btn{position:absolute;left:950px;top:59px;width:157px;height:42px;background:var(--ink);color:var(--white);border-radius:21px;display:flex;align-items:center;justify-content:center;font-size:14px;font-weight:700}

/* hero */
.hero{position:absolute;left:0;top:120px;width:1200px;height:640px;overflow:hidden}
.hero-media{position:absolute;inset:0;background:radial-gradient(ellipse at 70% 30%,#5A6F8C 0%,#2C3C55 40%,#141C2A 80%)}
.hero-title{position:absolute;left:0;top:104px;width:1200px;text-align:center;color:var(--white);font-size:41px;font-weight:500;line-height:51px;letter-spacing:.5px}
.hero-title .hl{color:var(--orange);font-weight:600}
.hero-sub{position:absolute;left:0;top:218px;width:1200px;text-align:center;color:var(--white);font-size:16.5px;line-height:28px}
.hero .btn{left:505px;top:295px;width:189px;height:41px}

/* section heading */
.sec-head{position:absolute;font-size:38px;font-weight:800;color:var(--ink);letter-spacing:.5px;line-height:44px}
.sec-head.light{color:var(--white)}

/* about */
.about-media{position:absolute;left:146px;top:778px;width:440px;height:440px;border-radius:50%;background:radial-gradient(circle at 45% 45%,#8C9AB0 0%,#3F4B61 45%,#1B2230 90%)}
.about-text{position:absolute;left:624px;top:914px;width:392px;font-size:13.4px;line-height:24px;text-align:justify;color:var(--text)}

/* products */
.products-bg{position:absolute;left:0;top:1282px}
.prod-card{position:absolute;width:300px;height:265px}
.prod-media{position:absolute;left:0;top:0;width:300px;height:232px}
.prod-label{position:absolute;left:16px;top:198px;width:268px;height:67px;background:var(--white);border:3px solid var(--orange);border-radius:4px;display:flex;align-items:center;justify-content:center;font-size:19px;font-weight:500;color:var(--ink)}

/* industries */
.ind-intro{position:absolute;left:127px;top:2578px;width:290px;font-size:12.5px;line-height:24px;color:var(--muted)}
.ind-card{position:absolute;width:294px;height:166px;border:2px solid var(--orange);border-radius:6px;background:var(--white)}
.ind-icon{position:absolute;left:18px;top:-42px;width:78px;height:78px;border-radius:50%;background:var(--orange)}
.ind-title{position:absolute;left:20px;top:58px;font-size:17px;font-weight:700;color:var(--ink)}
.ind-text{position:absolute;left:20px;top:94px;width:260px;font-size:12.5px;line-height:24px;color:var(--muted)}

/* blog */
.blog-card{position:absolute;width:310px;height:325px;background:var(--white);border-radius:6px;box-shadow:var(--card-shadow)}
.blog-media{position:absolute;left:8px;top:8px;width:294px;height:181px;border-radius:4px}
.blog-title{position:absolute;left:20px;top:210px;width:270px;font-size:17.5px;font-weight:700;line-height:27px;color:var(--ink)}
.blog-meta{position:absolute;left:20px;top:278px;display:flex;align-items:center;gap:10px;font-size:13.5px;font-weight:700;color:var(--ink)}
.blog-go{position:absolute;right:18px;top:276px}
.dots{position:absolute;left:570px;top:3409px;display:flex;gap:10px}
.dots i{display:block;width:12px;height:12px;border-radius:50%;border:2px solid var(--orange)}
.dots i.on{background:var(--orange)}

/* footer */
.footer-bg{position:absolute;left:0;top:3470px}
.partner{position:absolute;left:0;top:3662px;width:1200px;display:flex;justify-content:center;align-items:center;gap:14px;color:var(--white)}
.partner-sq{width:30px;height:30px;background:var(--orange)}
.partner-name{font-size:52px;font-weight:800;letter-spacing:4px}
.statement{position:absolute;left:0;top:3772px;width:1200px;text-align:center;color:var(--white);font-size:20.5px;font-weight:700;line-height:32px;letter-spacing:.3px}
.f-brand{position:absolute;left:122px;top:3918px;display:flex;align-items:center;gap:12px;color:var(--white)}
.f-brand .brand-name{color:var(--white);font-size:30px}
.f-brand .brand-rule{background:var(--white);height:44px}
.f-brand .brand-tag{color:var(--white);font-size:9px;line-height:12px;width:90px}
.f-col{position:absolute;top:3898px;color:var(--white)}
.f-col h4{font-size:17px;font-weight:600;margin-bottom:14px}
.f-links{list-style:none;font-size:14.5px}
.f-links li{height:33.5px;display:flex;align-items:flex-start;gap:10px}
.f-row{display:flex;gap:14px;font-size:14.5px;line-height:26px;margin-bottom:16px}
.f-row .nowrap{white-space:nowrap}
.f-ico{flex:none;width:30px;height:30px;border:1.5px solid var(--white);border-radius:50%;display:flex;align-items:center;justify-content:center}
.f-rule{position:absolute;left:119px;top:4138px;width:954px;height:1.5px;background:var(--white);opacity:.8}
.copy{position:absolute;left:0;top:4160px;width:1200px;text-align:center;color:var(--white);font-size:13px}
</style>
</head>
<body>

<header class="header">
  <div class="phone-tab">
    <span>USA</span>
    <svg width="16" height="16" viewBox="0 0 24 24"><path fill="#fff" d="M6.6 10.8a15 15 0 0 0 6.6 6.6l2.2-2.2a1 1 0 0 1 1-.25 11.4 11.4 0 0 0 3.6.57 1 1 0 0 1 1 1V20a1 1 0 0 1-1 1A17 17 0 0 1 3 4a1 1 0 0 1 1-1h3.5a1 1 0 0 1 1 1c0 1.25.2 2.45.57 3.57a1 1 0 0 1-.25 1z"/></svg>
    <span class="num">555-201-4470</span>
    <i class="sep"></i>
    <span>CANADA</span>
    <svg width="16" height="16" viewBox="0 0 24 24"><path fill="#fff" d="M6.6 10.8a15 15 0 0 0 6.6 6.6l2.2-2.2a1 1 0 0 1 1-.25 11.4 11.4 0 0 0 3.6.57 1 1 0 0 1 1 1V20a1 1 0 0 1-1 1A17 17 0 0 1 3 4a1 1 0 0 1 1-1h3.5a1 1 0 0 1 1 1c0 1.25.2 2.45.57 3.57a1 1 0 0 1-.25 1z"/></svg>
    <span class="num">555-201-4470</span>
  </div>
  <div class="brand">
    <i class="brand-dot"></i>
    <span class="brand-name">VORLAND</span>
    <i class="brand-rule"></i>
    <span class="brand-tag">Northgate Provisioning Trade Holdings</span>
  </div>
  <nav class="nav">
    <span class="active">HOME</span><span>ABOUT US</span><span>OUR PRODUCT</span><span>INDUSTRIES WE SERVE</span><span>BLOG</span>
  </nav>
  <div class="contact-btn">CONTACT US</div>
</header>

<section class="hero">
  <div class="hero-media" role="img" aria-label="Close-up of woven carbon fiber fabric in dark blue tones"></div>
  <svg class="abs" style="left:0;top:0" width="1200" height="640" viewBox="0 0 1200 640">
    <path d="M0 380 C280 560 720 620 1200 380 L1200 640 L0 640 Z" fill="#E8862A"/>
    <path d="M0 392 C300 560 720 596 1200 410 L1200 640 L0 640 Z" fill="#fff"/>
    <path d="M0 380 C120 440 160 450 0 405 Z" fill="#fff"/>
  </svg>
  <h1 class="hero-title">ADVANCED COMPOSITE MATERIALS<br>FOR THE <span class="hl">FUTURE OF INDUSTRY</span></h1>
  <p class="hero-sub">Importer &amp; Distributor of High-Performance Fibers and Composite<br>Materials across North America.</p>
  <div class="btn">REQUEST A QUOTE</div>
</section>

<!-- about -->
<svg class="abs" style="left:96px;top:770px" width="300" height="460" viewBox="0 0 300 460">
  <path d="M280 8 C120 0 10 110 10 230 C10 350 120 450 260 448 C150 420 60 340 60 230 C60 120 150 30 280 8 Z" fill="#E8862A"/>
</svg>
<div class="about-media" role="img" aria-label="Carbon fiber sheet running through an industrial processing machine"></div>
<h2 class="sec-head" style="left:647px;top:828px">ABOUT VORLAND</h2>
<p class="about-text">Lorem Ipsum is simply dummy text of the printing and typesetting industry. Lorem Ipsum has been the industry's standard dummy text ever since the 1500s, when an unknown printer took a galley of type and scrambled it to make a type specimen book. It has survived not only five centuries, but also the leap into electronic typesetting, remaining essentially unchanged. It was popularised in the 1960s with the release of Letraset sheets containing Lorem Ipsum passages</p>
<div class="btn" style="left:627px;top:1164px;width:163px;height:43px">READ MORE</div>

<!-- products -->
<svg class="products-bg" width="1200" height="1100" viewBox="0 0 1200 1100">
  <path d="M0 155 C300 40 800 -20 1080 30 Q1200 55 1200 200 L1200 840 C1100 1000 700 1110 300 1030 C150 995 50 960 0 906 Z" fill="#2A2623"/>
</svg>
<h2 class="sec-head light" style="left:435px;top:1444px">OUR PRODUCTS</h2>

<div class="prod-card" style="left:121px;top:1548px"><div class="prod-media" role="img" aria-label="Carbon fiber fabric" style="background:linear-gradient(160deg,#4A5566,#1C2330)"></div><div class="prod-label">Carbon Fiber</div></div>
<div class="prod-card" style="left:451px;top:1548px"><div class="prod-media" role="img" aria-label="Aramid fiber panels" style="background:linear-gradient(160deg,#6B6E73,#1E2022)"></div><div class="prod-label">Aramid Fiber</div></div>
<div class="prod-card" style="left:781px;top:1548px"><div class="prod-media" role="img" aria-label="Ribbed glass fiber sheet" style="background:linear-gradient(90deg,#C9CCCF,#8E9396,#D8DBDD)"></div><div class="prod-label">Glass Fiber</div></div>
<div class="prod-card" style="left:121px;top:1847px"><div class="prod-media" role="img" aria-label="Basalt fiber mat" style="background:linear-gradient(160deg,#B8B8B8,#8A8A8A)"></div><div class="prod-label">Basalt Fiber</div></div>
<div class="prod-card" style="left:451px;top:1847px"><div class="prod-media" role="img" aria-label="High silica glass wool" style="background:linear-gradient(160deg,#EDEDED,#B9B9B9)"></div><div class="prod-label">High Silica Glass</div></div>
<div class="prod-card" style="left:781px;top:1847px"><div class="prod-media" role="img" aria-label="Quartz fiber cloth" style="background:linear-gradient(135deg,#E9E6E0,#A9A49C)"></div><div class="prod-label">Quartz Fiber</div></div>
<div class="btn" style="left:516px;top:2170px;width:163px;height:44px">VIEW MORE</div>

<!-- industries -->
<h2 class="sec-head" style="left:168px;top:2473px">INDUSTRIES<br>WE SERVE</h2>
<p class="ind-intro">Lorem Ipsum is simply dummy text of the printing and typesetting industry.</p>

<div class="ind-card" style="left:446px;top:2479px"><i class="ind-icon" role="img" aria-label="Automotive robot arm icon"></i><div class="ind-title">Automotive</div><p class="ind-text">Lorem Ipsum is simply dummy text of the printing and typesetting industry.</p></div>
<div class="ind-card" style="left:769px;top:2479px"><i class="ind-icon" role="img" aria-label="Aerospace gear icon"></i><div class="ind-title">Aerospace</div><p class="ind-text">Lorem Ipsum is simply dummy text of the printing and typesetting industry.</p></div>
<div class="ind-card" style="left:127px;top:2703px"><i class="ind-icon" role="img" aria-label="Construction crane icon"></i><div class="ind-title">Construction</div><p class="ind-text">Lorem Ipsum is simply dummy text of the printing and typesetting industry.</p></div>
<div class="ind-card" style="left:446px;top:2703px"><i class="ind-icon" role="img" aria-label="Electrical plant icon"></i><div class="ind-title">Electrical</div><p class="ind-text">Lorem Ipsum is simply dummy text of the printing and typesetting industry.</p></div>
<div class="ind-card" style="left:769px;top:2703px"><i class="ind-icon" role="img" aria-label="Machinery icon"></i><div class="ind-title">Machinery</div><p class="ind-text">Lorem Ipsum is simply dummy text of the printing and typesetting industry.</p></div>

<!-- blog -->
<h2 class="sec-head" style="left:512px;top:2973px">OUR BLOG</h2>

<div class="blog-card" style="left:116px;top:3050px">
  <div class="blog-media" role="img" aria-label="Technician handling a glowing engine component" style="background:linear-gradient(135deg,#3E5B80,#1A2333)"></div>
  <div class="blog-title">Lorem Ipsum is simply dummy text of the printing</div>
  <div class="blog-meta"><svg width="28" height="28" viewBox="0 0 28 28"><circle cx="14" cy="14" r="12" fill="none" stroke="#2A2623" stroke-width="2"/><path d="M14 7v7l5 3" fill="none" stroke="#2A2623" stroke-width="2"/></svg>4 Min</div>
  <svg class="blog-go" width="30" height="30" viewBox="0 0 30 30"><circle cx="15" cy="15" r="14" fill="#E8862A"/><circle cx="15" cy="15" r="9" fill="none" stroke="#fff" stroke-width="1.5"/><path d="M11 15h8M16 12l3 3-3 3" fill="none" stroke="#fff" stroke-width="1.5"/></svg>
</div>
<div class="blog-card" style="left:444px;top:3050px">
  <div class="blog-media" role="img" aria-label="Turbine assembly in a factory" style="background:linear-gradient(135deg,#1E3550,#6A4A2A,#1A2333)"></div>
  <div class="blog-title">Lorem Ipsum is simply dummy text of the printing</div>
  <div class="blog-meta"><svg width="28" height="28" viewBox="0 0 28 28"><circle cx="14" cy="14" r="12" fill="none" stroke="#2A2623" stroke-width="2"/><path d="M14 7v7l5 3" fill="none" stroke="#2A2623" stroke-width="2"/></svg>4 Min</div>
  <svg class="blog-go" width="30" height="30" viewBox="0 0 30 30"><circle cx="15" cy="15" r="14" fill="#E8862A"/><circle cx="15" cy="15" r="9" fill="none" stroke="#fff" stroke-width="1.5"/><path d="M11 15h8M16 12l3 3-3 3" fill="none" stroke="#fff" stroke-width="1.5"/></svg>
</div>
<div class="blog-card" style="left:771px;top:3050px">
  <div class="blog-media" role="img" aria-label="Welding sparks in a metal workshop" style="background:linear-gradient(135deg,#1B2230,#7A4A20,#121820)"></div>
  <div class="blog-title">Lorem Ipsum is simply dummy text of the printing</div>
  <div class="blog-meta"><svg width="28" height="28" viewBox="0 0 28 28"><circle cx="14" cy="14" r="12" fill="none" stroke="#2A2623" stroke-width="2"/><path d="M14 7v7l5 3" fill="none" stroke="#2A2623" stroke-width="2"/></svg>4 Min</div>
  <svg class="blog-go" width="30" height="30" viewBox="0 0 30 30"><circle cx="15" cy="15" r="14" fill="#E8862A"/><circle cx="15" cy="15" r="9" fill="none" stroke="#fff" stroke-width="1.5"/><path d="M11 15h8M16 12l3 3-3 3" fill="none" stroke="#fff" stroke-width="1.5"/></svg>
</div>
<div class="dots"><i class="on"></i><i></i><i></i></div>

<!-- footer -->
<svg class="footer-bg" width="1200" height="738" viewBox="0 0 1200 738">
  <path d="M0 220 C300 70 700 20 1000 35 C1120 45 1180 90 1200 140 L1200 178 C1150 110 1000 78 850 82 C550 95 250 165 0 232 Z" fill="#E8862A"/>
  <path d="M0 242 C300 150 650 98 900 96 C1050 96 1150 130 1200 190 L1200 738 L0 738 Z" fill="#2A2623"/>
</svg>
<div class="partner"><i class="partner-sq"></i><span class="partner-name">BLORAN</span></div>
<p class="statement">WE ARE EXCLUSIVE SALES COMPANY IN NORTH AMERICA FOR BLORAN<br>COMPOSITES PRODUCED FROM CHINA AND THEIR OTHER ASIA FACILITIES.</p>

<div class="f-brand">
  <span class="brand-name">VORLAND</span>
  <i class="brand-rule"></i>
  <span class="brand-tag">Northgate Provisioning Trade Holdings</span>
</div>

<div class="f-col" style="left:414px">
  <h4>MAIN LINKS</h4>
  <ul class="f-links">
    <li><svg width="14" height="14" viewBox="0 0 14 14"><path d="M1 7h11M8 3l4 4-4 4" fill="none" stroke="#fff" stroke-width="2"/></svg>Home</li>
    <li><svg width="14" height="14" viewBox="0 0 14 14"><path d="M1 7h11M8 3l4 4-4 4" fill="none" stroke="#fff" stroke-width="2"/></svg>About Us</li>
    <li><svg width="14" height="14" viewBox="0 0 14 14"><path d="M1 7h11M8 3l4 4-4 4" fill="none" stroke="#fff" stroke-width="2"/></svg>Our Product</li>
    <li><svg width="14" height="14" viewBox="0 0 14 14"><path d="M1 7h11M8 3l4 4-4 4" fill="none" stroke="#fff" stroke-width="2"/></svg>Blog</li>
    <li><svg width="14" height="14" viewBox="0 0 14 14"><path d="M1 7h11M8 3l4 4-4 4" fill="none" stroke="#fff" stroke-width="2"/></svg>Contact</li>
  </ul>
</div>

<div class="f-col" style="left:583px;width:290px">
  <h4>USA</h4>
  <div class="f-row"><span class="f-ico"><svg width="14" height="16" viewBox="0 0 14 16"><path d="M7 15s5-5 5-9A5 5 0 0 0 2 6c0 4 5 9 5 9z" fill="none" stroke="#fff" stroke-width="1.5"/><circle cx="7" cy="6" r="1.8" fill="#fff"/></svg></span><span>18 Pinecrest Road, Laramie,<br>WY, USA 82070</span></div>
  <div class="f-row"><span class="f-ico"><svg width="14" height="14" viewBox="0 0 24 24"><path fill="#fff" d="M6.6 10.8a15 15 0 0 0 6.6 6.6l2.2-2.2a1 1 0 0 1 1-.25 11.4 11.4 0 0 0 3.6.57 1 1 0 0 1 1 1V20a1 1 0 0 1-1 1A17 17 0 0 1 3 4a1 1 0 0 1 1-1h3.5a1 1 0 0 1 1 1c0 1.25.2 2.45.57 3.57a1 1 0 0 1-.25 1z"/></svg></span><span>555-201-4470</span></div>
  <div class="f-row"><span class="f-ico"><svg width="14" height="12" viewBox="0 0 14 12"><rect x="1" y="1" width="12" height="10" fill="none" stroke="#fff" stroke-width="1.5"/><path d="M1 1l6 5 6-5" fill="none" stroke="#fff" stroke-width="1.5"/></svg></span><span class="nowrap">composites@vorland-example.com</span></div>
</div>

<div class="f-col" style="left:877px;width:300px">
  <h4>CANNADA</h4>
  <div class="f-row"><span class="f-ico"><svg width="14" height="16" viewBox="0 0 14 16"><path d="M7 15s5-5 5-9A5 5 0 0 0 2 6c0 4 5 9 5 9z" fill="none" stroke="#fff" stroke-width="1.5"/><circle cx="7" cy="6" r="1.8" fill="#fff"/></svg></span><span>240 Harbourline Drive,<br>Suite 310, Oakridge,<br>ON, K2P 4R8, Canada</span></div>
  <div class="f-row"><span class="f-ico"><svg width="14" height="14" viewBox="0 0 24 24"><path fill="#fff" d="M6.6 10.8a15 15 0 0 0 6.6 6.6l2.2-2.2a1 1 0 0 1 1-.25 11.4 11.4 0 0 0 3.6.57 1 1 0 0 1 1 1V20a1 1 0 0 1-1 1A17 17 0 0 1 3 4a1 1 0 0 1 1-1h3.5a1 1 0 0 1 1 1c0 1.25.2 2.45.57 3.57a1 1 0 0 1-.25 1z"/></svg></span><span>555-388-9152</span></div>
</div>

<i class="f-rule"></i>
<p class="copy">© 2025 Vorland I All Rights Reserved</p>

</body>
</html>
```